Looking for a cool & simple business-card-design for digital agency

Hi!

We are a web agency that offers Reputation Management, Vextor & Seo Services and software development. We like cool things, we like innovative styles.

We have uploaded our logo.

Project Deadline Extended Reason: Client does not want any designs with the colorful logo. Please send us submissions ONLY with the blac and white logo. What the client would like to see:1) Back of the card: is a silver logo on a black background2) front of the card with all the data, please use white background and black logo thank you Added Friday, May 8, 2015

Industry/Entity Type

Software

```html
<!DOCTYPE html>
<html lang="en">
<head>
<meta charset="utf-8">
<title>Nettaro – Business Card</title>
<link href="https://fonts.googleapis.com/css2?family=Open+Sans:wght@400;600;700&display=swap" rel="stylesheet">
<style>
  :root {
    --bg: #d9d9d9;
    --card-black: #141414;
    --card-white: #f7f7f5;
    --silver: #d4d4d4;
    --silver-dim: #9a9a9a;
    --ink: #1f1f1f;
    --teal: #1e9a9a;
    --green: #6fb33f;
    --magenta: #d6197f;
    --red: #d8262c;
    --orange: #f08a1c;
    --yellow: #f4e01c;
    --divider: #9c9c9c;
  }
  * { margin: 0; padding: 0; box-sizing: border-box; }
  html, body {
    width: 1200px; height: 852px; overflow: hidden;
    background: var(--bg);
    font-family: "Open Sans", Arial, sans-serif;
  }
  .stage { position: relative; width: 1200px; height: 852px; }

  .card {
    position: absolute;
    width: 540px; height: 310px;
    border-radius: 14px;
    overflow: hidden;
    box-shadow: 0 6px 18px rgba(0,0,0,.18);
  }

  /* Back of card */
  .card-back {
    left: 80px; top: 110px;
    background: var(--card-black);
    display: flex; align-items: center; justify-content: center; gap: 18px;
  }
  .card-back .mark {
    width: 22px; height: 22px; background: var(--silver);
  }
  .card-back .rule {
    width: 2px; height: 64px; background: var(--silver-dim);
  }
  .card-back .brand { display: flex; flex-direction: column; }
  .card-back .brand-name {
    color: var(--silver); font-weight: 700; font-size: 54px; line-height: 1;
    letter-spacing: 1px;
  }
  .card-back .tagline {
    color: var(--silver); font-weight: 400; font-size: 16px;
    letter-spacing: 6px; margin-top: 8px;
  }

  /* Front of card */
  .card-front {
    left: 580px; top: 430px;
    background: var(--card-white);
  }
  .card-front .brand-block {
    position: absolute; left: 40px; top: 110px;
    display: flex; align-items: center; gap: 12px;
  }
  .card-front .mark {
    width: 20px; height: 20px; border-radius: 50%; background: var(--ink);
  }
  .card-front .brand-name {
    color: var(--ink); font-weight: 700; font-size: 38px; line-height: 1;
  }
  .card-front .rule {
    position: absolute; left: 236px; top: 56px;
    width: 1px; height: 160px; background: var(--divider);
  }
  .card-front .details {
    position: absolute; left: 258px; top: 52px; color: var(--ink);
  }
  .person-name {
    color: var(--teal); font-weight: 700; font-size: 20px; line-height: 1.1;
  }
  .person-role { font-size: 12px; margin-top: 2px; }
  .contact-list { list-style: none; margin-top: 30px; font-size: 14px; }
  .contact-list li {
    display: flex; align-items: center; gap: 8px; line-height: 1.45;
  }
  .contact-list svg { width: 12px; height: 12px; fill: var(--teal); flex: none; }
  .contact-list .split { display: inline-flex; align-items: center; gap: 8px; }

  .colour-band {
    position: absolute; left: 0; bottom: 0; width: 540px; height: 40px;
  }
</style>
</head>
<body>
<main class="stage">

  <section class="card card-back" aria-label="Card back">
    <span class="mark" aria-hidden="true"></span>
    <span class="rule" aria-hidden="true"></span>
    <div class="brand">
      <span class="brand-name">Nettaro</span>
      <span class="tagline">DIGITALE STRATEGIEN</span>
    </div>
  </section>

  <section class="card card-front" aria-label="Card front">
    <div class="brand-block">
      <span class="mark" aria-hidden="true"></span>
      <span class="brand-name">Nettaro</span>
    </div>
    <span class="rule" aria-hidden="true"></span>

    <div class="details">
      <p class="person-name">Your Long Name</p>
      <p class="person-role">Managing Director</p>
      <ul class="contact-list">
        <li>
          <svg viewBox="0 0 12 12" aria-hidden="true"><path d="M6 0a4 4 0 0 0-4 4c0 3 4 8 4 8s4-5 4-8a4 4 0 0 0-4-4zm0 5.5A1.5 1.5 0 1 1 6 2.5a1.5 1.5 0 0 1 0 3z"/></svg>
          Your Commercial or office address
        </li>
        <li>
          <svg viewBox="0 0 12 12" aria-hidden="true"><path d="M2 1l2.5 0 1 3-1.5 1a7 7 0 0 0 3 3l1-1.5 3 1V11c-5 .5-10-4.5-9-10z"/></svg>
          <span class="split">00.00.00.0000
            <svg viewBox="0 0 12 12" aria-hidden="true"><path d="M3 0h6v3H3zM1 4h10v5H9v3H3V9H1zm3 4v3h4V8z"/></svg>
            00.00.00.0000</span>
        </li>
        <li>
          <svg viewBox="0 0 12 12" aria-hidden="true"><path d="M0 2h12v1L6 7 0 3zm0 2.2l6 4 6-4V10H0z"/></svg>
          yourname@yourwebsite.com
        </li>
        <li>
          <svg viewBox="0 0 12 12" aria-hidden="true"><circle cx="6" cy="6" r="5.5"/></svg>
          www.yourwebsite.com
        </li>
      </ul>
    </div>

    <svg class="colour-band" viewBox="0 0 540 40" preserveAspectRatio="none" aria-hidden="true">
      <polygon points="0,28 540,0 540,40 0,40" fill="var(--teal)"/>
      <polygon points="90,23.3 200,17.6 200,40 90,40" fill="var(--green)"/>
      <polygon points="200,17.6 300,12.4 300,40 200,40" fill="var(--magenta)"/>
      <polygon points="300,12.4 400,7.3 400,40 300,40" fill="var(--red)"/>
      <polygon points="400,7.3 470,3.6 470,40 400,40" fill="var(--orange)"/>
      <polygon points="470,3.6 540,0 540,40 470,40" fill="var(--yellow)"/>
    </svg>
  </section>

</main>
</body>
</html>
```